New Business Card Design Project LORVANTI-Italy

we are LORVANTI-Italy
our company in the market for 3 years we are luxury cosmetic company and its about time for a facelift :)
i will like to have elegant luxurious and unique business card
that will give the person that get it a unique, luxurious and elegant impression
I'm VERY OPEN FOR NEW IDEAS , even duo i add a few files of things that i see on line and i like them

i add my logo as well
my website is LORVANTI.COM
(if you would like to see the main style that we have)

Target Market(s)

adult that have money :)

Industry/Entity Type

Business

Contact Information for Business Card

Name - Dario Lorvanti
Position - CEO and CO Founder
address - 4817 E Halvern
telephone - 555-384-1926
email - dario@lorvanti.com
fax - 555-384-1926
website - LORVANTI.COM

Colors
000000
959595
fbee3e
ffffff

Requirements
Must have
• big logo in GOLD color
• elegant look
• impressive
Nice to have
• not must but maybe classy pattern background
• not must but maybe emblem
• maybe clear plastic business card
Should not have
• colors
• images

```html
<!DOCTYPE html>
<html lang="en">
<head>
<meta charset="UTF-8">
<title>LORVANTI Italy — Business Card</title>
<link href="https://fonts.googleapis.com/css2?family=Cormorant+Garamond:wght@500;600&display=swap" rel="stylesheet">
<style>
  :root {
    --backdrop: #1e1e1f;
    --ink: #2a2622;
    --band: #26231f;
    --gold-deep: #a8842f;
    --gold-mid: #c9aa55;
    --gold-light: #ead596;
    --gold-text: #d8b545;
  }
  * { margin: 0; padding: 0; box-sizing: border-box; }
  html, body {
    width: 1200px;
    height: 800px;
    overflow: hidden;
    background: var(--backdrop);
  }
  .card {
    position: absolute;
    left: 150px;
    top: 143px;
    width: 900px;
    height: 514px;
    border-radius: 34px;
    overflow: hidden;
    display: flex;
  }
  .card-face {
    position: relative;
    flex: 1;
    background: linear-gradient(125deg, var(--gold-deep) 0%, var(--gold-light) 38%, var(--gold-mid) 62%, var(--gold-deep) 100%);
  }
  .emblem {
    position: absolute;
    left: 50%;
    top: 50%;
    transform: translate(-50%, -50%);
    display: flex;
    flex-direction: column;
    align-items: center;
    gap: 18px;
  }
  .emblem-ring {
    width: 170px;
    height: 170px;
    border: 5px solid var(--ink);
    border-radius: 50%;
  }
  .emblem-name {
    font-family: "Cormorant Garamond", serif;
    font-weight: 600;
    font-size: 30px;
    letter-spacing: 6px;
    color: var(--ink);
  }
  .brand-band {
    position: relative;
    width: 230px;
    background: var(--band);
  }
  .brand-lockup {
    position: absolute;
    left: 50%;
    top: 50%;
    width: 380px;
    transform: translate(-50%, -50%) rotate(-90deg);
    font-family: "Cormorant Garamond", serif;
    color: var(--gold-text);
  }
  .brand-name {
    font-weight: 600;
    font-size: 74px;
    line-height: 0.9;
    letter-spacing: 1px;
    text-align: center;
  }
  .brand-rule {
    height: 3px;
    margin-top: 10px;
    background: var(--gold-text);
  }
  .brand-origin {
    font-weight: 600;
    font-size: 24px;
    letter-spacing: 2px;
    text-align: right;
    padding-right: 100px;
    margin-top: 6px;
  }
</style>
</head>
<body>
  <div class="card">
    <div class="card-face" role="img" aria-label="Gold background with fine geometric diamond pattern">
      <div class="emblem">
        <div class="emblem-ring"></div>
        <div class="emblem-name">LORVANTI</div>
      </div>
    </div>
    <div class="brand-band">
      <div class="brand-lockup">
        <div class="brand-name">LORVANTI</div>
        <div class="brand-rule"></div>
        <div class="brand-origin">ITALY</div>
      </div>
    </div>
  </div>
</body>
</html>
```